English and Spanish Language School Needs a Business Card

Need a business card design a startup company called Maribel Language School. The company will offer English and Spanish conversational level courses designed to make the learner feel comfortable with grammar and vocabulary. We would like to see a logo with some colour that should communicate learning, growth.

Target Market(s)

Consumers and businesses

Industry/Entity Type

Education

Contact Information for Business Card

TBD

Font styles to use
Serif

Requirements
Must have
• Include the following
• Logo
• Name
• Title
• Cellphone Number
• Office Phone number
• Email address
• Office Address

```html
<!DOCTYPE html>
<html lang="en">
<head>
<meta charset="utf-8">
<title>Maribel Language School – Business Card</title>
<link rel="stylesheet" href="https://fonts.googleapis.com/css2?family=Open+Sans:wght@400;600;700&display=swap">
<style>
  :root {
    --teal: #0ea0ab;
    --red: #d21f33;
    --ink: #2b2b2b;
    --muted: #4a4a4a;
    --paper: #ffffff;
    --backdrop: #e9eaec;
  }
  * { margin: 0; padding: 0; box-sizing: border-box; }
  html, body {
    width: 1200px; height: 900px; overflow: hidden;
    background: var(--backdrop);
    font-family: "Open Sans", Arial, sans-serif;
  }
  .canvas { position: relative; width: 1200px; height: 900px; }

  .card {
    position: absolute; left: 250px; width: 700px; height: 400px;
    overflow: hidden;
    box-shadow: 0 6px 18px rgba(0,0,0,0.18);
  }
  .card--back { top: 30px; background: var(--teal); }
  .card--front { top: 470px; background: var(--paper); }

  /* brand name as plain text */
  .brand {
    position: absolute; font-weight: 700; line-height: 1.05;
    letter-spacing: -0.5px;
  }
  .brand__name { display: block; font-size: 58px; }
  .brand__sub { display: block; font-size: 26px; font-weight: 700; }
  .card--back .brand { left: 210px; top: 130px; color: var(--paper); }
  .card--front .brand { left: 370px; top: 135px; color: var(--red); }

  .corner-mark { position: absolute; left: 0; top: 0; }

  .holder { position: absolute; left: 78px; top: 20px; }
  .holder__name { font-size: 20px; font-weight: 700; line-height: 1.15; }
  .holder__first { color: var(--red); }
  .holder__last { color: var(--teal); }
  .holder__title { font-size: 15px; color: var(--ink); }

  .contact {
    position: absolute; left: 34px; top: 170px;
    font-size: 16px; color: var(--ink); line-height: 1.45;
    list-style: none;
  }
  .contact__address { margin-bottom: 6px; margin-left: 24px; }
  .contact__item { display: flex; align-items: center; gap: 8px; }
  .contact__item svg { width: 16px; height: 16px; flex: none; }
  .contact__item--plain { padding-left: 24px; }

  .bands { position: absolute; left: 0; bottom: 0; }
</style>
</head>
<body>
<main class="canvas">

  <section class="card card--back" aria-label="Card back">
    <div class="brand">
      <span class="brand__name">Maribel</span>
      <span class="brand__sub">Language School</span>
    </div>
  </section>

  <section class="card card--front" aria-label="Card front">
    <svg class="corner-mark" width="70" height="60" viewBox="0 0 70 60" aria-hidden="true">
      <polygon points="0,18 22,18 10,40 0,40" fill="var(--red)"/>
      <polygon points="36,18 66,18 66,50 14,50" fill="var(--teal)"/>
    </svg>

    <div class="holder">
      <p class="holder__name"><span class="holder__first">Daniel</span> <span class="holder__last">Harper</span></p>
      <p class="holder__title">Managing Director</p>
    </div>

    <ul class="contact">
      <li class="contact__address">48 Harbour Lane, Suite 2<br>Westbridge, 502107.</li>
      <li class="contact__item">
        <svg viewBox="0 0 16 16" aria-hidden="true"><path d="M4 1.5l2.2 3-1.3 1.6c.8 1.8 2.3 3.3 4.1 4.1l1.6-1.3 3 2.2-1.2 2.6C7 13.5 2.5 9 1.6 3z" fill="var(--teal)"/></svg>
        044-555 218 307
      </li>
      <li class="contact__item">
        <svg viewBox="0 0 16 16" aria-hidden="true"><rect x="4" y="1" width="8" height="14" rx="1.5" fill="none" stroke="var(--teal)" stroke-width="1.6"/><circle cx="8" cy="12.3" r="0.9" fill="var(--teal)"/></svg>
        info@maribelschool.com
      </li>
      <li class="contact__item">
        <svg viewBox="0 0 16 16" aria-hidden="true"><rect x="1" y="3.5" width="14" height="9" fill="var(--teal)"/><path d="M1 3.5l7 5 7-5" fill="none" stroke="#fff" stroke-width="1.2"/></svg>
        www.maribelschool.com
      </li>
    </ul>

    <div class="brand">
      <span class="brand__name">Maribel</span>
      <span class="brand__sub">Language School</span>
    </div>

    <svg class="bands" width="700" height="70" viewBox="0 0 700 70" aria-hidden="true">
      <polygon points="0,0 300,0 282,30 0,30" fill="var(--red)"/>
      <polygon points="300,8 700,8 700,70 258,70" fill="var(--teal)"/>
      <polygon points="300,8 700,8 700,20 293,20" fill="var(--teal)"/>
    </svg>
  </section>

</main>
</body>
</html>
```